Newsletter Ad

I am looking for someone to design an advertisement for a mother's club newsletter. 4" wide X by 5" tall (and 2.5" wide X 5" tall if possible).

I'm a psychotherapist, so want the ad to look professional, but modern. I have a logo with my photo attached that can be incorporated into the design. The colors of my website are turquoise and white. I'd like to keep with that theme...so maybe some turquoise blocking to match the logo font color.

I'm uploading a logo as well as an ad draft with the content I'd like listed in the ad.

```html
<!DOCTYPE html>
<html lang="en">
<head>
<meta charset="utf-8">
<title>Clara Dove – Psychotherapy Ad</title>
<link href="https://fonts.googleapis.com/css2?family=Roboto+Condensed:wght@300;400;700&family=Lato:wght@300;400&display=swap" rel="stylesheet">
<style>
  :root {
    --teal: #4fa3a2;
    --white: #ffffff;
    --ink: #2b2b2b;
    --hero-top: #4a4a4a;
    --hero-bottom: #333333;
    --portrait-top: #2a2522;
    --portrait-bottom: #5a4a3e;
  }
  html, body {
    margin: 0;
    padding: 0;
    overflow: hidden;
    background: var(--white);
  }
  .ad {
    position: relative;
    width: 960px;
    height: 1200px;
    background: var(--teal);
    overflow: hidden;
    font-family: "Roboto Condensed", "Arial Narrow", sans-serif;
    color: var(--ink);
  }
  .hero-image {
    position: absolute;
    left: 36px;
    top: 36px;
    width: 888px;
    height: 539px;
    background: linear-gradient(160deg, var(--hero-top) 0%, var(--hero-bottom) 100%);
  }
  .headline {
    position: absolute;
    left: 36px;
    top: 575px;
    width: 888px;
    height: 64px;
    margin: 0;
    color: var(--white);
    font-weight: 700;
    font-size: 41px;
    line-height: 64px;
    text-align: center;
    letter-spacing: -0.2px;
    white-space: nowrap;
  }
  .panel {
    position: absolute;
    left: 36px;
    top: 639px;
    width: 888px;
    height: 525px;
    background: var(--white);
  }
  .services {
    position: absolute;
    left: 0;
    top: 24px;
    width: 888px;
    margin: 0;
    padding: 0;
    list-style: none;
  }
  .service-row {
    display: flex;
    justify-content: center;
    gap: 36px;
    height: 48px;
    align-items: center;
    font-size: 36px;
    font-weight: 300;
    letter-spacing: -0.4px;
  }
  .service {
    display: flex;
    align-items: center;
    gap: 26px;
    white-space: nowrap;
  }
  .service::before {
    content: "";
    width: 12px;
    height: 12px;
    background: var(--ink);
    transform: rotate(45deg);
    flex: none;
  }
  .portrait {
    position: absolute;
    left: 16px;
    top: 214px;
    width: 292px;
    height: 295px;
    background: linear-gradient(180deg, var(--portrait-top) 0%, var(--portrait-bottom) 100%);
  }
  .name {
    position: absolute;
    left: 324px;
    top: 440px;
    margin: 0;
    color: var(--teal);
    font-family: "Lato", sans-serif;
    font-weight: 300;
    font-size: 40px;
    line-height: 1;
    white-space: nowrap;
  }
  .credentials {
    position: absolute;
    left: 324px;
    width: 200px;
    top: 486px;
    margin: 0;
    color: var(--teal);
    font-family: "Lato", sans-serif;
    font-weight: 300;
    font-size: 22px;
    text-align: right;
  }
  .contact {
    position: absolute;
    right: 16px;
    top: 276px;
    margin: 0;
    font-style: normal;
    font-size: 28px;
    font-weight: 300;
    line-height: 35px;
    text-align: right;
  }
  .contact .phone {
    font-weight: 700;
  }
  .license {
    position: absolute;
    right: 16px;
    top: 486px;
    margin: 0;
    font-size: 22px;
    font-weight: 300;
  }
</style>
</head>
<body>
<div class="ad">
  <div class="hero-image" role="img" aria-label="Photo of cupped hands holding a white water lily"></div>
  <h1 class="headline">Psychotherapy for Individuals, Couples and Families</h1>
  <section class="panel">
    <ul class="services">
      <li class="service-row"><span class="service">Parenting</span><span class="service">Depression</span><span class="service">Anxiety</span><span class="service">Life Transitions</span></li>
      <li class="service-row"><span class="service">Divorce</span><span class="service">Couples Issues</span><span class="service">Women’s Issues</span></li>
      <li class="service-row"><span class="service">Attachment and Neuroscience</span></li>
    </ul>
    <div class="portrait" role="img" aria-label="Portrait photo of the therapist"></div>
    <p class="name">CLARA DOVE</p>
    <p class="credentials">MA, MFT</p>
    <address class="contact">
      418 Harbor Lane<br>
      Cedar Glen, CA 94900<br>
      www.claradove.com<br>
      clara@claradove.com<br>
      <span class="phone">415 555 0142</span>
    </address>
    <p class="license">License# MFC48213</p>
  </section>
</div>
</body>
</html>
```